Brivolt Technologies business card design

We need a business card designed with our new logo. it would be great if the card could communicate it is a technology based company.

Target Market(s)

system integrators

Industry/Entity Type

technology, IOT

Contact Information for Business Card

Name, designation, Address, telephone number, email address

Requirements
Must have
• logo and company name
Nice to have
• something to do with technology

```html
<!DOCTYPE html>
<html lang="en">
<head>
<meta charset="utf-8">
<title>Brivolt Technologies business card</title>
<link rel="stylesheet" href="https://fonts.googleapis.com/css2?family=Open+Sans:ital,wght@0,400;0,700;1,400&display=swap">
<style>
  :root {
    --stage: #2b2b2b;
    --card: #1a1a1a;
    --card-deep: #111111;
    --pattern-tone: #2a2a2a;
    --accent: #f39019;
    --ink: #ffffff;
    --ink-soft: #d9d9d9;
  }
  * { margin: 0; padding: 0; box-sizing: border-box; }
  html, body { width: 1200px; height: 900px; overflow: hidden; }
  body {
    background: var(--stage);
    font-family: "Open Sans", Arial, sans-serif;
    position: relative;
  }
  .card {
    position: absolute;
    left: 250px;
    width: 700px;
    height: 400px;
    background: var(--card);
    border-bottom: 3px solid var(--accent);
    border-left: 2px solid var(--accent);
    overflow: hidden;
    box-shadow: 0 12px 30px rgba(0,0,0,0.5);
  }
  .card-front { top: 35px; }
  .card-back { top: 465px; }

  .brand {
    position: relative;
    z-index: 1;
    display: flex;
    align-items: center;
    gap: 12px;
    color: var(--ink);
    font-weight: 700;
    font-size: 30px;
    letter-spacing: 1px;
    text-transform: uppercase;
  }
  .brand-mark {
    width: 18px;
    height: 18px;
    background: var(--accent);
  }
  .card-front .brand { position: absolute; left: 46px; top: 44px; }

  .address {
    position: absolute;
    left: 46px;
    top: 140px;
    color: var(--ink-soft);
    font-size: 17px;
    line-height: 26px;
  }
  .contact-list {
    position: absolute;
    left: 46px;
    top: 218px;
    list-style: none;
    color: var(--ink-soft);
    font-size: 17px;
    line-height: 28px;
  }
  .contact-list li { display: flex; align-items: center; gap: 10px; }
  .contact-list svg { width: 15px; height: 15px; fill: var(--accent); flex: none; }

  .holder {
    position: absolute;
    right: 46px;
    top: 150px;
    text-align: right;
    z-index: 1;
  }
  .holder-name {
    color: var(--accent);
    font-weight: 700;
    font-size: 24px;
    letter-spacing: 1px;
    text-transform: uppercase;
  }
  .holder-role {
    color: var(--ink);
    font-style: italic;
    font-size: 18px;
  }

  .front-decor {
    position: absolute;
    left: 290px;
    right: 0;
    top: 210px;
    bottom: 0;
    background:
      radial-gradient(ellipse 70% 90% at 55% 100%, #3a3a3a 0%, #2a2a2a 45%, rgba(26,26,26,0) 100%);
  }

  .back-pattern {
    position: absolute;
    inset: 0;
    background:
      radial-gradient(ellipse 60% 70% at 80% 85%, #2e2e2e 0%, rgba(46,46,46,0) 70%),
      radial-gradient(ellipse 55% 60% at 15% 20%, #242424 0%, rgba(36,36,36,0) 70%),
      linear-gradient(135deg, var(--card-deep) 0%, #1b1b1b 50%, #252525 100%);
  }
  .card-back .brand {
    position: absolute;
    right: 60px;
    top: 200px;
    font-size: 34px;
  }
</style>
</head>
<body>

  <section class="card card-front">
    <div class="front-decor" role="img" aria-label="Large faint embossed brand symbol decoration"></div>

    <div class="brand">
      <span class="brand-mark"></span>
      <span class="brand-name">Brivolt Technologies</span>
    </div>

    <p class="address">1480 Seacliff Harbor<br>Bayview CA 90417</p>

    <ul class="contact-list">
      <li>
        <svg viewBox="0 0 16 16" aria-hidden="true"><path d="M3.5 1l2.5 3-1.5 1.8c.9 2 2.5 3.6 4.5 4.5L10.8 8.8l3 2.5-1.3 3C7 14 2 9 1.7 2.4z"/></svg>
        555-012-4387
      </li>
      <li>
        <svg viewBox="0 0 16 16" aria-hidden="true"><path d="M1 3h14v10H1z M1 3l7 6 7-6" stroke="#1a1a1a" stroke-width="1.2"/></svg>
        info@brivolttech.com
      </li>
      <li>
        <svg viewBox="0 0 16 16" aria-hidden="true"><circle cx="8" cy="8" r="7"/><path d="M1 8h14M8 1c3 3 3 11 0 14M8 1c-3 3-3 11 0 14" stroke="#1a1a1a" stroke-width="1.1" fill="none"/></svg>
        www.brivolttech.com
      </li>
    </ul>

    <div class="holder">
      <p class="holder-name">Darren Kolway</p>
      <p class="holder-role">President</p>
    </div>
  </section>

  <section class="card card-back">
    <div class="back-pattern" role="img" aria-label="Repeating faint embossed brand symbol pattern covering the card back"></div>
    <div class="brand">
      <span class="brand-mark"></span>
      <span class="brand-name">Brivolt Technologies</span>
    </div>
  </section>

</body>
</html>
```